Copperleaf Roofing Business Card

This is my current business card. But I’d like to make some changes. Somewhere on the card I’d like to list some of the services we offer. Maybe on the back? But I’d still like to keep the red. White and black modern look.

-residential & commercial roofing
-Roof Repairs & Maintenance
-Storm Damage & Insurance Claims specialist
-Christmas Lights and permanent Christmas lights
Fencing. Windows. Gutters. Siding. Sheetrock, painting.

```html
<!DOCTYPE html>
<html lang="en">
<head>
<meta charset="utf-8">
<title>Copperleaf Roofing Co. – Business Card</title>
<link rel="stylesheet" href="https://fonts.googleapis.com/css2?family=Michroma&family=Open+Sans:wght@400;700&display=swap">
<style>
  :root {
    --stage: #2e2e30;
    --red: #e01b22;
    --red-deep: #8e0f14;
    --black: #111111;
    --white: #ffffff;
    --ink-soft: #2a2a2a;
  }
  * { box-sizing: border-box; margin: 0; padding: 0; }
  html, body { width: 1200px; height: 694px; overflow: hidden; }
  body {
    background: var(--stage);
    font-family: "Open Sans", Arial, sans-serif;
    position: relative;
  }
  .card {
    position: absolute;
    top: 192px;
    width: 540px;
    height: 310px;
    border-radius: 22px;
    overflow: hidden;
  }
  /* Back of card */
  .card-back { left: 30px; }
  .tartan-field {
    position: absolute; inset: 0;
    background:
      linear-gradient(135deg, var(--red) 0%, var(--red-deep) 45%, var(--red) 70%, #5a0a0d 100%);
  }
  .back-brand {
    position: absolute;
    left: 0; right: 0; top: 58px;
    display: flex; align-items: center; justify-content: center; gap: 16px;
  }
  .brand-dot {
    width: 64px; height: 64px; border-radius: 50%;
    background: var(--black);
    border: 4px solid var(--white);
    flex-shrink: 0;
  }
  .back-brand .brand-name {
    font-family: "Michroma", Arial, sans-serif;
    color: var(--white);
    font-size: 24px;
    line-height: 1.2;
    letter-spacing: 1px;
  }
  .services {
    position: absolute;
    left: 30px; right: 30px; bottom: 34px;
    list-style: none;
    display: flex; flex-wrap: wrap; justify-content: center;
    gap: 4px 14px;
    color: var(--white);
    font-weight: 700;
    font-size: 13px;
    text-align: center;
  }
  .services li::before { content: "• "; }

  /* Front of card */
  .card-front { left: 630px; background: var(--white); }
  .emblem-field {
    position: absolute;
    right: 34px; top: 40px;
    width: 200px; height: 200px;
    border-radius: 50%;
    background: radial-gradient(circle at 40% 40%, var(--red) 0%, var(--red) 55%, var(--red-deep) 100%);
  }
  .front-brand {
    position: absolute;
    left: 34px; top: 66px;
    font-family: "Michroma", Arial, sans-serif;
    color: var(--red);
    font-size: 26px;
    line-height: 1.25;
    letter-spacing: 1px;
  }
  .person {
    position: absolute;
    left: 34px; top: 176px;
  }
  .person-name {
    font-family: "Michroma", Arial, sans-serif;
    color: var(--red);
    font-size: 17px;
    letter-spacing: 1px;
  }
  .person-role {
    color: var(--ink-soft);
    font-size: 14px;
    margin-top: 2px;
  }
  .contacts {
    list-style: none;
    margin-top: 12px;
    display: grid; gap: 4px;
    color: var(--black);
    font-size: 13.5px;
  }
  .contacts li { display: flex; align-items: center; gap: 8px; }
  .contacts svg { width: 14px; height: 14px; fill: var(--red); flex-shrink: 0; }
</style>
</head>
<body>

<section class="card card-back" aria-label="Card back">
  <div class="tartan-field" role="img" aria-label="Red, black and white tartan plaid background"></div>
  <div class="back-brand">
    <span class="brand-dot"></span>
    <span class="brand-name">COPPERLEAF<br>ROOFING CO.</span>
  </div>
  <ul class="services">
    <li>Residential &amp; commercial roofing</li>
    <li>Roof Repairs &amp; Maintenance</li>
    <li>Storm Damage &amp; Insurance Claims specialist</li>
    <li>Christmas Lights and permanent Christmas lights</li>
    <li>Fencing</li>
    <li>Windows</li>
    <li>Siding</li>
    <li>Sheetrock</li>
    <li>Painting</li>
  </ul>
</section>

<section class="card card-front" aria-label="Card front">
  <div class="emblem-field" role="img" aria-label="Brand emblem area on a red circle"></div>
  <div class="front-brand">COPPERLEAF<br>ROOFING CO.</div>
  <div class="person">
    <p class="person-name">DANA WHITFIELD</p>
    <p class="person-role">Owner</p>
    <ul class="contacts">
      <li>
        <svg viewBox="0 0 24 24" aria-hidden="true"><path d="M6.6 10.8a15.1 15.1 0 0 0 6.6 6.6l2.2-2.2a1 1 0 0 1 1-.25 11.4 11.4 0 0 0 3.6.57 1 1 0 0 1 1 1V20a1 1 0 0 1-1 1A17 17 0 0 1 3 4a1 1 0 0 1 1-1h3.5a1 1 0 0 1 1 1c0 1.25.2 2.45.57 3.57a1 1 0 0 1-.25 1z"/></svg>
        555-014-2290
      </li>
      <li>
        <svg viewBox="0 0 24 24" aria-hidden="true"><path d="M2 5h20v14H2zm2 2v.5l8 5 8-5V7l-8 5z"/></svg>
        dana@copperleafroofing.co
      </li>
      <li>
        <svg viewBox="0 0 24 24" aria-hidden="true"><path d="M12 2a10 10 0 1 0 0 20 10 10 0 0 0 0-20zm6.9 6h-3a15 15 0 0 0-1.3-4 8 8 0 0 1 4.3 4zM12 4c.8 1.2 1.5 2.5 1.9 4h-3.8c.4-1.5 1.1-2.8 1.9-4zM4.3 14a8 8 0 0 1 0-4h3.4a16 16 0 0 0 0 4zm.8 2h3a15 15 0 0 0 1.3 4 8 8 0 0 1-4.3-4zm3-8h-3a8 8 0 0 1 4.3-4 15 15 0 0 0-1.3 4zM12 20c-.8-1.2-1.5-2.5-1.9-4h3.8c-.4 1.5-1.1 2.8-1.9 4zm2.3-6H9.7a14 14 0 0 1 0-4h4.6a14 14 0 0 1 0 4zm.3 6a15 15 0 0 0 1.3-4h3a8 8 0 0 1-4.3 4zm1.7-6a16 16 0 0 0 0-4h3.4a8 8 0 0 1 0 4z"/></svg>
        www.copperleafroofing.co
      </li>
    </ul>
  </div>
</section>

</body>
</html>
```